GivingGavelHub Website Redesign

I'm looking to give our website a new look and feel with better graphics/images and that is focused on conversions.
www.givinggavelhub.example. The content can stay the same. Im looking for a new hero section with maybe a call to auction form to create an auction by asking for the following information: Event Name, Event Benefits, Country, Time zone and currency.
Our goal is to show that we can host online auctions, mobile auctions and live in-person auction. The content does not need to change on the site. We just need sections or illustrations that represent those features. It would also be good to have a sections that will segment our users into the following categories: Nonprofits/Charities, Schools/Education, Businesses, Government Agency, Individual.
The following pages need to be updated:
https://www.givinggavelhub.example/
https://www.givinggavelhub.example/online-bidding-features
https://www.givinggavelhub.example/online-bidding-experience
https://www.givinggavelhub.example/about
https://www.givinggavelhub.example/pricing
Updates
This project would cover the following 4 pages:
https://www.givinggavelhub.example

```html
<!DOCTYPE html>
<html lang="en">
<head>
<meta charset="utf-8">
<title>GivingGavelHub – Online Auction Platform</title>
<link rel="stylesheet" href="https://fonts.googleapis.com/css2?family=League+Spartan:wght@400;500;600&family=Lato:wght@400;700&display=swap">
<style>
:root{
  --blue:#2f80ed;
  --blue-deep:#1b58b8;
  --navy:#1a4fa0;
  --ink:#1e1e2a;
  --text:#3d3d48;
  --muted:#6b6b78;
  --line:#e3e6ee;
  --soft:#f3f4f8;
  --white:#fff;
  --black:#0b0b0d;
  --star:#f5c518;
}
*{box-sizing:border-box;margin:0;padding:0}
html,body{width:1200px;height:4777px;overflow:hidden}
body{position:relative;background:var(--white);font-family:"Lato",sans-serif;color:var(--text)}
.abs{position:absolute}
.heading{font-family:"League Spartan",sans-serif;font-weight:500;text-transform:uppercase;letter-spacing:2px;color:var(--ink)}
.btn{position:absolute;display:flex;align-items:center;justify-content:center;border-radius:6px;font-family:"League Spartan",sans-serif;font-weight:500;font-size:14px;letter-spacing:1px;text-transform:uppercase;text-decoration:none}
.btn-solid{background:var(--blue);color:var(--white)}
/* header */
.site-header{position:absolute;left:0;top:0;width:1200px;height:82px;background:var(--white);border-bottom:1px solid var(--line)}
.brand{position:absolute;display:flex;align-items:center;gap:10px;font-family:"League Spartan",sans-serif;font-weight:600;color:var(--blue)}
.brand .dot{border-radius:50%;background:var(--blue)}
.nav{position:absolute;left:495px;top:30px;display:flex;gap:22px;font-size:14px;color:var(--ink)}
.nav-btn{position:absolute;top:22px;height:38px;border-radius:5px;color:var(--white);font-size:13px;font-weight:700;display:flex;align-items:center;justify-content:center}
/* hero */
.hero{position:absolute;left:0;top:82px;width:1200px;height:597px;background:linear-gradient(110deg,#1f5fc4 0%,#2a74de 55%,#3a86ec 100%);overflow:hidden}
.hero-shape{position:absolute;background:rgba(255,255,255,.07);border-radius:40px;transform:rotate(45deg)}
.hero-title{position:absolute;left:108px;top:100px;width:640px;font-size:41px;line-height:56px;color:var(--white);letter-spacing:3px}
.hero-text{position:absolute;left:111px;top:292px;width:560px;font-size:15px;line-height:26px;color:#eaf1ff}
.hero-btn{top:398px;height:46px;font-size:13px}
.create-card{position:absolute;left:733px;top:78px;width:356px;height:413px;background:var(--white);border-radius:10px}
.create-card h2{position:absolute;top:42px;width:100%;text-align:center;font-size:22px;letter-spacing:2px}
.field{position:absolute;left:37px;width:285px;height:32px;border:1px solid #cfd3dc;border-radius:3px;font-size:10px;color:var(--ink);padding:0 16px;display:flex;align-items:center;justify-content:space-between}
.field svg{width:10px;height:10px}
.create-btn{position:absolute;left:37px;top:335px;width:285px;height:32px;background:var(--navy);color:var(--white);border-radius:3px;font-size:10px;font-weight:700;letter-spacing:1px;display:flex;align-items:center;justify-content:center}
/* section titles */
.section-title{position:absolute;left:0;width:1200px;text-align:center;font-size:34px;letter-spacing:3px}
/* categories */
.cat{position:absolute;top:824px;width:176px;height:137px;background:var(--white);border-radius:6px;box-shadow:0 6px 22px rgba(30,40,80,.12);display:flex;flex-direction:column;align-items:center;justify-content:flex-end;padding-bottom:22px;text-align:center}
.cat svg{width:62px;height:56px;margin-bottom:10px}
.cat span{font-family:"League Spartan",sans-serif;font-size:12px;font-weight:500;letter-spacing:1px;line-height:18px;color:var(--ink)}
/* features */
.ring{position:absolute;border:2px dashed #cfd2da;border-radius:50%}
.photo{position:absolute;border-radius:50%}
.feat-title{position:absolute;font-size:24px;line-height:35px;letter-spacing:2px;width:460px}
.feat-text{position:absolute;width:445px;font-size:14.5px;line-height:26px;color:var(--text)}
.quote{position:absolute;width:427px;background:var(--white);border-radius:6px;box-shadow:0 8px 28px rgba(30,40,80,.13);padding:28px 20px 20px 44px}
.stars{color:var(--star);font-size:15px;letter-spacing:3px;margin-bottom:6px}
.quote p{font-size:13px;line-height:26px;color:var(--ink)}
.quote .who{margin-top:12px;font-family:"League Spartan",sans-serif;font-size:13px;color:var(--ink);letter-spacing:.5px}
.quote .who b{font-weight:600}
.avatar{position:absolute;width:56px;height:56px;border-radius:50%;background:linear-gradient(135deg,#c9a58a,#7a5a4a)}
.feat-btn{height:60px;width:223px;font-size:14px}
/* company */
.crowd{position:absolute;left:0;top:2430px;width:1200px;height:816px;background:linear-gradient(180deg,rgba(255,255,255,1) 0%,rgba(236,205,200,.55) 30%,rgba(214,160,150,.7) 60%,rgba(196,150,160,.75) 100%)}
.partner{position:absolute;top:3030px;width:140px;height:140px;display:flex;align-items:center;justify-content:center}
/* faq */
.faq-card{position:absolute;left:158px;top:3428px;width:883px;height:594px;background:var(--white);border-radius:60px;box-shadow:0 10px 40px rgba(30,40,80,.12)}
.faq-row{position:absolute;left:46px;width:800px;height:66px;background:var(--soft);border-radius:33px;display:flex;align-items:center}
.faq-row.open{background:var(--white)}
.faq-num{width:60px;height:60px;margin-left:3px;border-radius:50%;background:var(--white);border:3px solid var(--blue);display:flex;align-items:center;justify-content:center;font-family:"League Spartan",sans-serif;font-weight:600;font-size:24px;color:var(--navy);letter-spacing:1px}
.faq-row.open .faq-num{background:var(--blue);color:var(--white)}
.faq-q{margin-left:28px;font-family:"League Spartan",sans-serif;font-size:19px;letter-spacing:1px;color:var(--ink);flex:1}
.faq-icon{margin-right:32px;font-size:24px;color:var(--blue);font-weight:300}
.faq-answer{position:absolute;left:138px;top:436px;width:640px;border-left:2px solid var(--blue-deep);padding-left:16px;font-size:14px;line-height:26px;color:var(--ink)}
.faq-answer a{color:var(--blue)}
.more{position:absolute;left:575px;top:3998px;width:48px;height:48px;border-radius:50%;background:var(--white);box-shadow:0 4px 14px rgba(30,40,80,.15);display:flex;align-items:center;justify-content:center}
/* footer */
.footer{position:absolute;left:0;top:4356px;width:1200px;height:421px;background:var(--black)}
.cta{position:absolute;left:167px;top:4109px;width:866px;height:297px;background:linear-gradient(110deg,#1a4fa6,#235fbd);border-radius:10px;text-align:center;color:var(--white)}
.cta h2{position:absolute;top:70px;width:100%;font-size:33px;color:var(--white);letter-spacing:3px}
.cta p{position:absolute;top:132px;width:100%;font-family:"League Spartan",sans-serif;font-size:15px;letter-spacing:2px;text-transform:uppercase}
.foot-title{position:absolute;font-size:21px;color:var(--white);letter-spacing:2px}
.foot-links{position:absolute;left:623px;top:4508px;list-style:none;font-size:14px;line-height:30px;color:#e6e6ea}
.foot-links li::before{content:"« ";color:#cfd2da}
.news-input{position:absolute;left:811px;top:4513px;width:278px;height:41px;border:1px solid #55575e;border-radius:4px;font-size:12px;color:#b8bac2;padding:0 16px;display:flex;align-items:center}
.news-btn{position:absolute;left:811px;top:4567px;width:278px;height:41px;background:var(--navy);border-radius:4px;color:var(--white);font-family:"League Spartan",sans-serif;font-size:15px;letter-spacing:1px;display:flex;align-items:center;justify-content:center}
.social{position:absolute;top:4559px;width:28px;height:28px;border-radius:50%;background:#2a2b30}
.copy{position:absolute;left:0;top:4717px;width:1200px;text-align:center;font-size:14px;color:#e6e6ea}
.copy a{color:var(--blue)}
</style>
</head>
<body>

<header class="site-header">
  <div class="brand" style="left:110px;top:22px;font-size:27px"><span class="dot" style="width:36px;height:36px"></span>GivingGavelHub</div>
  <nav class="nav"><span>How It Works</span><span>Pricing</span><span>About</span><span>Blog</span></nav>
  <svg class="abs" style="left:793px;top:33px" width="16" height="16" viewBox="0 0 16 16"><circle cx="6.5" cy="6.5" r="5" fill="none" stroke="#1e1e2a" stroke-width="2"/><line x1="10" y1="10" x2="15" y2="15" stroke="#1e1e2a" stroke-width="2"/></svg>
  <div class="nav-btn" style="left:824px;width:106px;background:var(--navy)">For Bidders</div>
  <div class="nav-btn" style="left:948px;width:141px;background:var(--blue)">For Fundraisers</div>
</header>

<section class="hero">
  <div class="hero-shape" style="left:900px;top:-80px;width:260px;height:520px"></div>
  <div class="hero-shape" style="left:1050px;top:200px;width:180px;height:420px"></div>
  <div class="hero-shape" style="left:640px;top:380px;width:160px;height:300px"></div>
  <h1 class="heading hero-title">You’ve just found the easiest online auction platform to use, period.</h1>
  <p class="hero-text">GivingGavelHub has eliminated the headache of setting up online and in-person auctions. We’ve simplified everything to get you up and running quickly without the help of a tech team.</p>
  <a class="btn hero-btn btn-solid" style="left:111px;width:158px;background:#3b8cf5">Online Auctions</a>
  <a class="btn hero-btn" style="left:282px;width:206px;border:2px solid #9cc1f5;color:var(--white)">Live In-Person Auctions</a>
  <a class="btn hero-btn" style="left:497px;width:158px;background:var(--white);color:var(--navy)">Mobile Auctions</a>

  <form class="create-card">
    <h2 class="heading">Create Event</h2>
    <div class="field" style="top:174px">Name your event</div>
    <div class="field" style="top:222px">Event Benefits</div>
    <div class="field" style="top:269px">Country*<svg viewBox="0 0 10 10"><path d="M2 3.5L5 6.5 8 3.5" fill="none" stroke="#333" stroke-width="1.4"/></svg></div>
    <div class="field" style="top:315px;">Time Zone*<svg viewBox="0 0 10 10"><path d="M2 3.5L5 6.5 8 3.5" fill="none" stroke="#333" stroke-width="1.4"/></svg></div>
    <div class="field" style="top:363px">Currency*<svg viewBox="0 0 10 10"><path d="M2 3.5L5 6.5 8 3.5" fill="none" stroke="#333" stroke-width="1.4"/></svg></div>
    <div class="create-btn" style="top:413px">CREATE NEW EVENT</div>
  </form>
</section>

<h2 class="heading section-title" style="top:742px">Categories</h2>
<div class="cat" style="left:100px"><svg viewBox="0 0 62 56" fill="none" stroke="#2f80ed" stroke-width="2"><path d="M31 50C12 36 6 27 6 18a12 12 0 0 1 25-6 12 12 0 0 1 25 6c0 9-6 18-25 32z"/><path d="M20 30l8 6 14-14"/></svg><span>Nonprofits<br>Charities</span></div>
<div class="cat" style="left:306px"><svg viewBox="0 0 62 56" fill="none" stroke="#2f80ed" stroke-width="2"><path d="M4 52h54M8 52V26h46v26M20 26V14l11-8 11 8v12M26 52V40h10v12"/><rect x="13" y="32" width="6" height="6"/><rect x="43" y="32" width="6" height="6"/><circle cx="31" cy="18" r="3"/></svg><span>Schools<br>Education</span></div>
<div class="cat" style="left:512px"><svg viewBox="0 0 62 56" fill="none" stroke="#2f80ed" stroke-width="2"><circle cx="31" cy="14" r="7"/><circle cx="14" cy="22" r="5"/><circle cx="48" cy="22" r="5"/><path d="M19 44c0-10 6-16 12-16s12 6 12 16M4 42c0-7 4-11 10-11M58 42c0-7-4-11-10-11"/></svg><span>Businesses</span></div>
<div class="cat" style="left:718px"><svg viewBox="0 0 62 56" fill="none" stroke="#2f80ed" stroke-width="2"><path d="M8 20L31 6l23 14zM10 20h42M14 24v20M24 24v20M38 24v20M48 24v20M8 46h46M5 52h52"/></svg><span>Government<br>Agencies</span></div>
<div class="cat" style="left:924px"><svg viewBox="0 0 62 56" fill="none" stroke="#2f80ed" stroke-width="2"><path d="M6 42l12-6h14c3 0 3 5 0 5H22M6 52l10-4h20l18-12c3-2 0-6-3-4L38 38"/><rect x="24" y="12" width="14" height="16" rx="2"/><path d="M28 12V8h6v4"/></svg><span>Individuals</span></div>

<h2 class="heading section-title" style="top:1082px">Spend less time. Make more money.</h2>

<!-- feature 1 -->
<div class="ring" style="left:114px;top:1202px;width:452px;height:452px"></div>
<div class="photo" role="img" aria-label="Person using a laptop showing a donation screen" style="left:145px;top:1233px;width:390px;height:390px;background:linear-gradient(140deg,#6fb6df,#3b6a8a 60%,#2b2f35)"></div>
<h3 class="heading feat-title" style="left:647px;top:1201px">Quickly create, design and manage auctions.</h3>
<p class="feat-text" style="left:647px;top:1280px">You are only 5 minutes away from having your auction built and ready for items. We took the pain and confusion out of getting started.</p>
<div class="quote" style="left:664px;top:1376px"><div class="stars">★★★★★</div><p>“I’m 74 years old and I didn’t need to call my Grandkids to set up this auction for me! The software was easy to use and the end of auction experience was a breeze!”</p><div class="who"><b>Marla K. -</b> Lakeside Service Club</div></div>
<div class="avatar" role="img" aria-label="Reviewer portrait" style="left:634px;top:1385px"></div>
<a class="btn btn-solid feat-btn" style="left:647px;top:1577px">Build an Auction</a>

<!-- feature 2 -->
<h3 class="heading feat-title" style="left:128px;top:1767px">More money goes directly to your cause.</h3>
<p class="feat-text" style="left:128px;top:1845px">You can accept cash, checks, bank transfers, or credit cards. It’s your money, collect it on your own terms.</p>
<div class="quote" style="left:145px;top:1942px"><div class="stars">★★★★★</div><p>“We just completed an auction that raised over $30,000 for a family battling cancer. GivingGavelHub made it possible with very little cost. 100% we will use them again.”</p><div class="who"><b>Daniel Ostrow -</b> Harbor Family Fund</div></div>
<div class="avatar" role="img" aria-label="Reviewer portrait" style="left:115px;top:1951px"></div>
<a class="btn btn-solid feat-btn" style="left:128px;top:2143px">Collect More Money</a>
<div class="ring" style="left:608px;top:1754px;width:480px;height:480px"></div>
<div class="photo" role="img" aria-label="Hand holding a phone photographing an auction item" style="left:635px;top:1781px;width:426px;height:426px;background:radial-gradient(circle at 45% 45%,#8a5a4a,#c98a7a 45%,#e8d6d0 80%)"></div>

<!-- feature 3 -->
<div class="crowd" role="img" aria-label="Cheering children with raised hands"></div>
<div class="ring" style="left:126px;top:2321px;width:452px;height:452px;background:rgba(255,255,255,.4)"></div>
<div class="photo" role="img" aria-label="Tablet and phone showing a make a donation screen" style="left:157px;top:2352px;width:390px;height:390px;background:linear-gradient(135deg,#bfc4cc,#e7e9ee 50%,#9aa1ab)"></div>
<h3 class="heading feat-title" style="left:647px;top:2318px">Manage your donors and donations effortlessly.</h3>
<p class="feat-text" style="left:647px;top:2395px">Our Donation CRM allows you to easily track all donations and donors in an easy-to-use dashboard. Export all information or sync with our integration partners to unlock more donor management tools.</p>
<div class="quote" style="left:664px;top:2523px"><div class="stars">★★★★★</div><p>“The people coming to our events say it’s easy to use and we can check people out so much faster than we ever could in the past. I highly recommend trying GivingGavelHub out, you’ll never go anywhere else.”</p><div class="who"><b>Owen Petrak -</b> Riverbend Rovers</div></div>
<div class="avatar" role="img" aria-label="Reviewer portrait" style="left:634px;top:2531px"></div>
<a class="btn btn-solid feat-btn" style="left:647px;top:2745px">Manage My Donors</a>

<h2 class="heading section-title" style="top:2893px">You’re in good company</h2>
<p class="abs" style="left:0;top:2950px;width:1200px;text-align:center;font-family:'League Spartan',sans-serif;font-size:20px;letter-spacing:1.5px;color:var(--ink)">Here are some other organizations that have run auctions with us:</p>
<div class="partner" style="left:288px"><svg width="90" height="80"><rect x="5" y="10" width="80" height="60" rx="8" fill="#5b3f8f"/></svg></div>
<div class="partner" style="left:443px;width:162px;height:148px;top:3024px;background:var(--white);border:2px solid #4f7fd6;border-radius:4px"><svg width="60" height="60"><circle cx="30" cy="30" r="26" fill="#5a3a86"/></svg></div>
<div class="partner" style="left:622px"><svg width="100" height="100"><circle cx="50" cy="50" r="40" fill="#e1501f"/></svg></div>
<div class="partner" style="left:789px"><svg width="90" height="90"><rect x="10" y="15" width="70" height="60" fill="#3a2a12"/></svg></div>

<h2 class="heading section-title" style="top:3343px">Frequently asked questions</h2>
<div class="faq-card">
  <div class="faq-row" style="top:43px"><div class="faq-num">01</div><div class="faq-q">Can I Pass Fees Onto Bidders?</div><div class="faq-icon">+</div></div>
  <div class="faq-row" style="top:143px"><div class="faq-num">02</div><div class="faq-q">What Happens If Items Don't Sell?</div><div class="faq-icon">+</div></div>
  <div class="faq-row" style="top:245px"><div class="faq-num">03</div><div class="faq-q">Can I Download All My Bidder Data?</div><div class="faq-icon">+</div></div>
  <div class="faq-row open" style="top:351px"><div class="faq-num">04</div><div class="faq-q">What Is The Management Fee?</div><div class="faq-icon">–</div></div>
  <p class="faq-answer">The management fee is a fee we charge to use our platform. If you select our free plan, we will charge a 5% management fee of the total amount raised. For example, if your auction raises $1000, we will collect a $50 management fee. Depending on your auction goals and size, you could limit management fees by choosing a prepaid plan. <a href="#">Read More</a></p>
</div>
<div class="more"><svg width="14" height="14" viewBox="0 0 14 14"><path d="M3 5l4 4 4-4" fill="none" stroke="#2f80ed" stroke-width="1.8"/></svg></div>

<footer class="footer">
  <div class="brand" style="left:102px;top:96px;font-size:38px;font-weight:500"><span class="dot" style="width:60px;height:60px"></span>GivingGavelHub</div>
  <span class="social" style="left:284px;background:var(--blue)"></span>
  <span class="social" style="left:322px"></span>
  <span class="social" style="left:358px"></span>
  <span class="social" style="left:394px"></span>
  <h4 class="heading foot-title" style="left:623px;top:106px">Help Links</h4>
  <h4 class="heading foot-title" style="left:811px;top:106px">Get Our Newsletter</h4>
  <p class="copy" style="top:361px">©Copyrights 2023 <a href="#">GivingGavelHub</a> | &nbsp; All Rights Reserved</p>
</footer>
<ul class="foot-links"><li>Terms &amp; Conditions</li><li>Privacy Policy</li><li>About Us</li><li>Support</li></ul>
<div class="news-input">Enter Your Email</div>
<div class="news-btn">SUBSCRIBE NOW</div>

<section class="cta">
  <h2 class="heading">Let’s get started, it’s super easy.</h2>
  <p>Oh yeah, you don’t need a credit card to get started either.</p>
  <a class="btn btn-solid" style="left:321px;top:187px;width:224px;height:60px">Build an Auction</a>
</section>

</body>
</html>
```